Facebook ad design for Glimmerloft

Design 6 x FB ads for online jewellery store (South Africa) selling bracelets, charms and rings. Use high quality images which do not have any copyright restrictions. Please advise regarding optimal size for high FB ads. (1080 x 1080 pixels?) The logo of the business is attached in uploaded file. It is not necessary to use the logo on ads. The ads must look professional and clear. Additional text will be added on the ads by the owner. Do not stick to color scheme of the site or FB page. So do not use the pink. The main requirement is that the ads must look very professional. The website will also be redesigned.
https://glimmerloft.example/
https://www.facebook.com/GlimmerLoft.example
The ads must specifically be designed for and target the following days.
1 for mother's day
1 for valentine's day
1 for Christmas
1 with love theme
2 general to target female jewellery lovers (bracelets / charms)

Alternatively you can create 10 images for FB carousel ad (1080 x 1080 pixels) with products from the actual website. Use high quality images from the web, but use products that is listed on the Glimmerloft website. Use your imagination. Simple, modern and elegant.

Target Market(s)

Ladies / Woman

Font styles to use
Sans Serif

Colors

Designer to choose colors to be used in the design.

Requirements
Nice to have
• Professional / Modern / Elegant ads

```html
<!DOCTYPE html>
<html lang="en">
<head>
<meta charset="utf-8">
<title>Glimmerloft — Valentine's Day</title>
<link rel="stylesheet" href="https://fonts.googleapis.com/css2?family=Cormorant+Garamond:wght@500&family=Pinyon+Script&display=swap">
<style>
  :root {
    --rose-deep: #b80d14;
    --rose-mid: #e0222a;
    --rose-light: #f2464a;
    --band: #7f0b0e;
    --tile: #ffffff;
    --silver-light: #eef0f3;
    --silver-mid: #c9ccd2;
    --ink-light: #ffffff;
  }
  * { margin: 0; padding: 0; box-sizing: border-box; }
  html, body {
    width: 1200px;
    height: 1200px;
    overflow: hidden;
    background: var(--rose-deep);
  }
  .ad {
    position: relative;
    width: 1200px;
    height: 1200px;
    overflow: hidden;
  }
  .rose-backdrop {
    position: absolute;
    inset: 0;
    background:
      radial-gradient(circle at 20% 15%, var(--rose-light) 0%, transparent 35%),
      radial-gradient(circle at 80% 30%, var(--rose-light) 0%, transparent 30%),
      radial-gradient(circle at 30% 85%, var(--rose-light) 0%, transparent 35%),
      radial-gradient(circle at 85% 85%, var(--rose-mid) 0%, transparent 40%),
      linear-gradient(160deg, var(--rose-mid), var(--rose-deep));
  }
  .brand {
    position: absolute;
    top: 120px;
    left: 0;
    width: 100%;
    text-align: center;
    font-family: "Cormorant Garamond", serif;
    font-weight: 500;
    font-size: 74px;
    letter-spacing: 2px;
    text-transform: uppercase;
    color: var(--ink-light);
  }
  .product-band {
    position: absolute;
    top: 417px;
    left: 0;
    width: 1200px;
    height: 362px;
    background: var(--band);
  }
  .product-tile {
    position: absolute;
    top: 31px;
    width: 370px;
    height: 306px;
    background: var(--tile);
  }
  .product-tile.necklace { left: 18px; }
  .product-tile.ring { left: 413px; }
  .product-tile.bracelet { left: 810px; }
  .product-photo {
    position: absolute;
    inset: 40px 60px;
    border-radius: 8px;
    background: radial-gradient(ellipse at center, var(--silver-mid) 0%, var(--silver-light) 55%, var(--tile) 100%);
  }
  .headline {
    position: absolute;
    left: 0;
    top: 800px;
    width: 1200px;
    font-family: "Pinyon Script", cursive;
    color: var(--ink-light);
    font-size: 170px;
    line-height: 1;
  }
  .headline .line-one { position: absolute; left: 300px; top: 20px; white-space: nowrap; }
  .headline .line-two { position: absolute; left: 640px; top: 165px; white-space: nowrap; }
</style>
</head>
<body>
  <main class="ad">
    <div class="rose-backdrop" role="img" aria-label="Close-up background of deep red rose petals"></div>

    <div class="brand">Glimmerloft</div>

    <section class="product-band">
      <div class="product-tile necklace">
        <div class="product-photo" role="img" aria-label="Silver pendant necklace with a round sparkling stone in a heart-trimmed halo"></div>
      </div>
      <div class="product-tile ring">
        <div class="product-photo" role="img" aria-label="Silver openwork ring with flower cut-outs and pink enamel blossoms, engraved inside"></div>
      </div>
      <div class="product-tile bracelet">
        <div class="product-photo" role="img" aria-label="Silver snake-chain bracelet with a pavé heart clasp"></div>
      </div>
    </section>

    <h1 class="headline">
      <span class="line-one">Valentine’s</span>
      <span class="line-two">Day!</span>
    </h1>
  </main>
</body>
</html>
```